Visitenkarten-Design für virtuelle Jobmesse & Jobbörse für Soldaten
Zielgruppe
Die KVL GmbH ist ein Unternehmen das zwei Hauptprodukte betreibt! Zum einen Jobbörse für Soldaten unter www.laufbahnwechsel-beispiel.de und zum anderen eine virtuelle Jobmesse für Soldaten unter www.merivon-beispiel.de , die wir zweimal im Jahr veranstalten.
Aufgabenstellung
Wir haben ja die beiden Produkte Laufbahnwechsel.de und die Merivon, für die bereits jeweils ein separtes Logo besteht! Diese finden Sie im Anhang! Beide werden doch jedoch von einem Unternehmen, der KVL GmbH betrieben! Aktuell nutzen wir eine Visitenkarte mit dem Logo von KVL und eine mit dem Logo der MERIVON. Gerade im Hinblick darauf, dass wir zukünftig auch weiter Plattformen in unser Portfolio aufnehmen, möchte ich hier unsere V-Karten flexibler gestalten!
Ziel soll es also sein, eine Visitenkarte zu gestalten, auf dem klar wird, dass der Mitarbeiter von der KVL GmbH kommt, die KVL GmbH aber unterschiedliche Produkte betreibt.
Im Anhang finden Sie:
1. Das Logo von KVL
2. Das Logo von Merivon
3. Die aktuelle V-Karte von KVL
4. Die aktuelle V-Karte von MERIVON
Vielleicht ein kleiner Anreiz: Aktuell nutzen wir auch zwei getrennte Geschäftspapiere. Das von www.laufbahnwechsel-beispiel.de lade ich einmal hoch! Der Designer, der auch die Visitenkarte erstellt, erhällt im Anschluss den 1:1 Auftrag in Höhe von 200 Euro für die Erstellung des Geschäftspapiers! Wenn Sie jetzt schon einen Vorschlag für das Geschäftspapier einreichen, erhöht das natürlich Ihre Chancen, wobei ich verspreche, dass wir im Falle eine Annahme das 1:1 im Anschluß dennoch starten werden!

```html
<!DOCTYPE html>
<html lang="de">
<head>
<meta charset="utf-8">
<title>Visitenkarten KVL GmbH</title>
<link rel="stylesheet" href="https://fonts.googleapis.com/css2?family=Montserrat:wght@400;500;700&display=swap">
<style>
  :root {
    --blue: #2a5189;
    --green: #3b5b29;
    --paper: #ffffff;
    --stage-light: #c3c3c3;
    --stage-dark: #a9a9a9;
    --desk: #d8d2c8;
    --desk-2: #cfc8bc;
  }
  * { box-sizing: border-box; margin: 0; padding: 0; }
  html, body { width: 1200px; height: 2801px; overflow: hidden; }
  body { position: relative; font-family: "Montserrat", Arial, sans-serif; background: var(--desk); }

  .stage { position: absolute; left: 0; width: 1200px; }
  .stage-flat { top: 0; height: 1200px; background: var(--stage-light); }
  .stage-flat svg { position: absolute; inset: 0; }
  .stage-desk { height: 800px; background: linear-gradient(180deg, var(--desk-2), var(--desk)); }
  .stage-desk.first { top: 1200px; border-top: 1px solid #bdb6aa; }
  .stage-desk.second { top: 2000px; height: 801px; border-top: 1px solid #bdb6aa; }

  .card {
    position: absolute; width: 658px; height: 376px; background: var(--paper);
    box-shadow: 6px 12px 18px rgba(0,0,0,0.22);
    color: var(--accent);
  }
  .card.blue { --accent: var(--blue); }
  .card.green { --accent: var(--green); }
  .card > * { position: absolute; white-space: nowrap; }

  .brand { left: 40px; top: 76px; display: flex; align-items: center; gap: 10px; font-size: 21px; font-weight: 700; line-height: 1; color: var(--accent); }
  .brand .mark { width: 18px; height: 18px; background: var(--accent); }
  .brand .mark.round { border-radius: 50%; }

  .company { right: 41px; top: 56px; font-size: 26px; font-weight: 700; line-height: 1; }
  .company-bar { left: 626px; top: 50px; width: 5px; height: 40px; background: var(--accent); }

  .person { right: 46px; top: 147px; text-align: right; }
  .person .name { font-size: 28px; font-weight: 700; line-height: 1; }
  .person .role { font-size: 17px; font-weight: 500; line-height: 1; margin-top: 6px; }

  .rule { height: 8px; border-top: 3px solid var(--accent); border-bottom: 2px solid var(--accent); top: 183px; }
  .rule.left { left: 0; width: 460px; }
  .rule.right { left: 624px; width: 34px; }

  .contact { left: 28px; font-size: 18px; line-height: 1; }
  .contact.email { top: 214px; }
  .contact.phone { top: 253px; }
  .contact.mobile { top: 277px; }
  .contact.web { top: 308px; font-weight: 700; font-size: 17.5px; }

  .address { right: 47px; top: 244px; text-align: right; font-size: 17.5px; line-height: 25px; }
  .address-bar { left: 627px; top: 248px; width: 3px; height: 42px; background: var(--accent); }

  .band { left: 0; bottom: 0; width: 658px; height: 27px; background: var(--accent); }
</style>
</head>
<body>

<section class="stage stage-flat">
  <svg width="1200" height="1200" viewBox="0 0 1200 1200" aria-hidden="true">
    <polygon points="1200,0 1200,560 560,1200 0,1200" fill="#aaaaaa"/>
    <polygon points="1200,560 1200,1200 560,1200" fill="#b3b3b3"/>
  </svg>

  <article class="card blue" style="left:260px;top:175px;">
    <div class="brand"><span class="mark"></span>Laufbahnwechsel.de</div>
    <div class="company">KVL GmbH</div><div class="company-bar"></div>
    <div class="person"><div class="name">Jonas Berger</div><div class="role">Geschäftsführer</div></div>
    <div class="rule left"></div><div class="rule right"></div>
    <div class="contact email">jonas.berger@laufbahnwechsel-beispiel.de</div>
    <div class="contact phone">T: 0831 - 555 20 17</div>
    <div class="contact mobile">M: 0170 - 555 31 942</div>
    <div class="contact web">www.laufbahnwechsel-beispiel.de</div>
    <div class="address">Lindenweg 14<br>86999 Musterfeld</div><div class="address-bar"></div>
    <div class="band"></div>
  </article>

  <article class="card green" style="left:260px;top:630px;">
    <div class="brand"><span class="mark round"></span>MERIVON</div>
    <div class="company">KVL GmbH</div><div class="company-bar"></div>
    <div class="person"><div class="name">Jonas Berger</div><div class="role">Geschäftsführer</div></div>
    <div class="rule left"></div><div class="rule right"></div>
    <div class="contact email">jonas.berger@merivon-beispiel.de</div>
    <div class="contact phone">T: 0831 - 555 20 17</div>
    <div class="contact mobile">M: 0170 - 555 31 942</div>
    <div class="contact web">www.merivon-beispiel.de</div>
    <div class="address">Lindenweg 14<br>86999 Musterfeld</div><div class="address-bar"></div>
    <div class="band"></div>
  </article>
</section>

<section class="stage stage-desk first">
  <article class="card blue" style="left:271px;top:212px;">
    <div class="brand"><span class="mark"></span>Laufbahnwechsel.de</div>
    <div class="company">KVL GmbH</div><div class="company-bar"></div>
    <div class="person"><div class="name">Jonas Berger</div><div class="role">Geschäftsführer</div></div>
    <div class="rule left"></div><div class="rule right"></div>
    <div class="contact email">jonas.berger@laufbahnwechsel-beispiel.de</div>
    <div class="contact phone">T: 0831 - 555 20 17</div>
    <div class="contact mobile">M: 0170 - 555 31 942</div>
    <div class="contact web">www.laufbahnwechsel-beispiel.de</div>
    <div class="address">Lindenweg 14<br>86999 Musterfeld</div><div class="address-bar"></div>
    <div class="band"></div>
  </article>
</section>

<section class="stage stage-desk second">
  <article class="card green" style="left:271px;top:212px;">
    <div class="brand"><span class="mark round"></span>MERIVON</div>
    <div class="company">KVL GmbH</div><div class="company-bar"></div>
    <div class="person"><div class="name">Jonas Berger</div><div class="role">Geschäftsführer</div></div>
    <div class="rule left"></div><div class="rule right"></div>
    <div class="contact email">jonas.berger@merivon-beispiel.de</div>
    <div class="contact phone">T: 0831 - 555 20 17</div>
    <div class="contact mobile">M: 0170 - 555 31 942</div>
    <div class="contact web">www.merivon-beispiel.de</div>
    <div class="address">Lindenweg 14<br>86999 Musterfeld</div><div class="address-bar"></div>
    <div class="band"></div>
  </article>
</section>

</body>
</html>
```